Venture 482 - Lumora Book Cover

I am looking for a Lumora book cover for my book about "Venture 482".
The Book is Titled:
Venture 482 Ascended
Shaping Outcomes: Paths To Unlocking Cosmic Truths
Author is Dorian Pell
Here is a book description that may help you understand more about it:
Inspired by the genius of Edwin Marlowe, this comprehensive guide delves into the ancient wisdom and cutting-edge science behind the 482 method, a powerful tool for manifesting your desires. Whether you're seeking personal growth, financial success, or spiritual enlightenment, this book provides advanced techniques and methods to transform your dreams into reality.
Any questions please ask.
Thanks
Owen

```html
<!DOCTYPE html>
<html lang="en">
<head>
<meta charset="utf-8">
<title>Venture 482 Ascended — Dorian Pell</title>
<link rel="stylesheet" href="https://fonts.googleapis.com/css2?family=Anton&family=Montserrat:wght@400;700;800;900&family=Rubik+Dirt&display=swap">
<style>
  :root {
    --red-core: #e11a28;
    --red-mid: #b5151f;
    --red-deep: #7c101a;
    --red-edge: #4f0c16;
    --ink-white: #ffffff;
    --accent-gold: #f6b300;
    --shadow: rgba(40, 0, 6, 0.65);
  }
  html, body {
    margin: 0;
    padding: 0;
    width: 805px;
    height: 1200px;
    overflow: hidden;
    background: var(--red-edge);
  }
  .cover {
    position: relative;
    width: 805px;
    height: 1200px;
    overflow: hidden;
  }
  .cover-art {
    position: absolute;
    inset: 0;
    width: 805px;
    height: 1200px;
    display: block;
  }
  .series-word {
    font-family: "Montserrat", sans-serif;
    font-weight: 800;
    fill: var(--ink-white);
  }
  .series-number {
    font-family: "Anton", sans-serif;
    fill: var(--ink-white);
    filter: drop-shadow(6px 8px 6px var(--shadow));
  }
  .edition {
    font-family: "Montserrat", sans-serif;
    font-weight: 700;
    fill: var(--ink-white);
  }
  .subtitle-lead {
    font-family: "Montserrat", sans-serif;
    font-weight: 400;
    fill: var(--ink-white);
  }
  .subtitle-tagline {
    font-family: "Montserrat", sans-serif;
    font-weight: 800;
    fill: var(--accent-gold);
  }
  .author {
    font-family: "Rubik Dirt", "Anton", sans-serif;
    fill: var(--ink-white);
  }
</style>
</head>
<body>
<main class="cover">
  <svg class="cover-art" viewBox="0 0 805 1200" xmlns="http://www.w3.org/2000/svg">
    <defs>
      <radialGradient id="ring-shade" cx="240" cy="660" r="900" gradientUnits="userSpaceOnUse">
        <stop offset="0" stop-color="#e8202d"/>
        <stop offset="0.35" stop-color="#c3161f"/>
        <stop offset="0.7" stop-color="#8a111b"/>
        <stop offset="1" stop-color="#4f0c16"/>
      </radialGradient>
      <radialGradient id="emblem-glow" cx="0.5" cy="0.5" r="0.5">
        <stop offset="0" stop-color="#ffffff" stop-opacity="0.28"/>
        <stop offset="0.7" stop-color="#ffffff" stop-opacity="0.12"/>
        <stop offset="1" stop-color="#ffffff" stop-opacity="0"/>
      </radialGradient>
    </defs>

    <g class="backdrop">
      <rect width="805" height="1200" fill="url(#ring-shade)"/>
      <g fill="none" stroke="#3a0510" stroke-opacity="0.18" stroke-width="18">
        <circle cx="240" cy="660" r="150"/>
        <circle cx="240" cy="660" r="250"/>
        <circle cx="240" cy="660" r="350"/>
        <circle cx="240" cy="660" r="450"/>
        <circle cx="240" cy="660" r="550"/>
        <circle cx="240" cy="660" r="650"/>
        <circle cx="240" cy="660" r="750"/>
        <circle cx="240" cy="660" r="850"/>
      </g>
    </g>

    <circle class="emblem" cx="604" cy="322" r="150" fill="url(#emblem-glow)"
            role="img" aria-label="Sacred geometry emblem of circles and radiating lines"/>

    <text class="series-word" x="116" y="329" font-size="92" textLength="338" lengthAdjust="spacingAndGlyphs">VENTURE</text>
    <text class="series-number" x="195" y="604" font-size="330" textLength="454" lengthAdjust="spacingAndGlyphs">482</text>
    <text class="edition" x="151" y="680" font-size="74" textLength="506" lengthAdjust="spacing">ASCENDED</text>

    <text class="subtitle-lead" x="402.5" y="831" font-size="44" text-anchor="middle">SHAPING OUTCOMES:</text>
    <text class="subtitle-tagline" x="402.5" y="902" font-size="37" text-anchor="middle">Paths to unlocking</text>
    <text class="subtitle-tagline" x="402.5" y="946" font-size="37" text-anchor="middle">cosmic truths</text>

    <text class="author" x="67" y="1151" font-size="104" textLength="675" lengthAdjust="spacing">DORIAN PELL</text>
  </svg>
</main>
</body>
</html>
```